Business Card Design

We are a manufacturing and distribution company with most of our customer base being supermarkets. We have established brand guidelines that are attached.

```html
<!DOCTYPE html>
<html lang="en">
<head>
<meta charset="utf-8">
<title>NORVEDA — Business Card</title>
<link href="https://fonts.googleapis.com/css2?family=Arimo:wght@400;700&display=swap" rel="stylesheet">
<style>
  :root{
    --bg:#e4e4e2;
    --white:#ffffff;
    --ink:#1a1a1a;
    --blue:#0d62ad;
    --blue-light:#2b7fcb;
    --blue-deep:#0a4f8e;
    --red:#e3252b;
    --grey:#6d6d6d;
  }
  *{box-sizing:border-box;margin:0;padding:0}
  html,body{width:1200px;height:802px;overflow:hidden}
  body{background:var(--bg);font-family:"Arimo",Arial,sans-serif;position:relative}

  .card{
    position:absolute;top:246px;width:540px;height:309px;
    border-bottom:3px solid var(--red);
    box-shadow:0 10px 24px rgba(0,0,0,.14);
    overflow:hidden;
  }
  .card--front{left:40px;background:var(--white)}
  .card--back{left:620px;background:var(--blue)}

  /* front */
  .brand{position:absolute;left:44px;top:40px;display:flex;align-items:center;gap:14px}
  .brand__square{width:30px;height:30px;background:var(--red)}
  .brand__name{font-weight:700;font-size:46px;letter-spacing:1px;color:var(--ink);line-height:1}

  .person{position:absolute;left:44px;top:112px}
  .person__name{color:var(--red);font-weight:700;font-size:17px;letter-spacing:.5px;text-transform:uppercase}
  .person__role{color:var(--grey);font-size:14px;margin-top:3px}

  .band{
    position:absolute;left:0;right:0;top:168px;height:104px;
    background:var(--blue);display:flex;align-items:center;padding-left:44px;color:var(--white);
  }
  .contacts{list-style:none;font-size:14.5px;line-height:1.45}
  .contacts li{display:flex;align-items:center;gap:10px}
  .contacts svg{width:12px;height:12px;flex:none}
  .divider{width:1px;height:64px;background:rgba(255,255,255,.55);margin:0 22px}
  .address{font-style:normal;font-size:14.5px;line-height:1.45}

  .band__tab{
    position:absolute;right:0;top:0;width:88px;height:104px;
    background:var(--white);border-radius:0 0 0 22px;
    display:flex;align-items:center;justify-content:center;
  }
  .band__tab span{width:40px;height:40px;background:var(--red)}

  /* back */
  .back__texture{
    position:absolute;inset:0;
    background:linear-gradient(135deg,var(--blue-deep) 0%,var(--blue) 50%,var(--blue-light) 100%);
  }
  .back__brand{
    position:absolute;left:0;right:0;top:50%;transform:translateY(-50%);
    display:flex;align-items:center;justify-content:center;gap:16px;
  }
  .back__square{width:36px;height:36px;background:var(--red)}
  .back__name{font-weight:700;font-size:40px;letter-spacing:1px;color:var(--white);line-height:1}
</style>
</head>
<body>

<section class="card card--front">
  <div class="brand">
    <span class="brand__square"></span>
    <span class="brand__name">NORVEDA</span>
  </div>

  <div class="person">
    <p class="person__name">Elliot Marsh</p>
    <p class="person__role">Manager</p>
  </div>

  <div class="band">
    <ul class="contacts">
      <li>
        <svg viewBox="0 0 12 12"><path d="M3 1l2 2.4-1.2 1.3a6 6 0 0 0 3.5 3.5L8.6 7 11 9l-1 2C5 11 1 7 1 2z" fill="var(--red)"/></svg>
        555-010-2100
      </li>
      <li>
        <svg viewBox="0 0 12 12"><rect x="1" y="2.5" width="10" height="7" fill="none" stroke="var(--red)" stroke-width="1.3"/><path d="M1 2.5l5 4 5-4" fill="none" stroke="var(--red)" stroke-width="1.3"/></svg>
        hello@norveda.com
      </li>
      <li>
        <svg viewBox="0 0 12 12"><circle cx="6" cy="6" r="5" fill="none" stroke="var(--red)" stroke-width="1.3"/><path d="M1 6h10M6 1c-2.5 3-2.5 7 0 10M6 1c2.5 3 2.5 7 0 10" fill="none" stroke="var(--red)" stroke-width="1.1"/></svg>
        www.norveda.com
      </li>
    </ul>
    <span class="divider"></span>
    <address class="address">Your address<br>city<br>state, ZIP 0000</address>
    <div class="band__tab"><span></span></div>
  </div>
</section>

<section class="card card--back">
  <div class="back__texture" role="img" aria-label="Embossed repeating brand-mark pattern in tones of blue"></div>
  <div class="back__brand">
    <span class="back__square"></span>
    <span class="back__name">NORVEDA</span>
  </div>
</section>

</body>
</html>
```